Tidewell Homecare

I am looking to have a website designed for a housekeeping company that looks similar to this one. https://marloweshomecare.example/

I need 5 websites designed but will start with this one to see how I like it.

Industry/Entity Type

House Cleaning

Coding

Coded - Design and coding required

Number of Pages Required

5+ page

Font styles to use
Serif
Script

Colors
ffffff
fdf9cf
fbf289
fbee3f
d6edf3
86cae7
33a6d7
edf1f8
cedeed

```html
<!DOCTYPE html>
<html lang="en">
<head>
<meta charset="utf-8">
<title>Contact Us – Tidewell Homecare</title>
<link rel="stylesheet" href="https://fonts.googleapis.com/css2?family=Oswald:wght@400;500&family=Poppins:wght@300;400;500&display=swap">
<style>
:root{
  --blue:#0a9ae6;
  --blue-deep:#0680c6;
  --blue-light:#08aef5;
  --ink:#222222;
  --text:#555555;
  --muted:#8a8a8a;
  --line:#dcdcdc;
  --dark:#2a2a2a;
  --white:#ffffff;
  --hero-a:#e6ebef;
  --hero-b:#cfd8de;
}
*{margin:0;padding:0;box-sizing:border-box}
html,body{width:1020px;height:1200px;overflow:hidden;background:var(--white)}
body{position:relative;font-family:"Poppins",sans-serif;color:var(--text)}
.abs{position:absolute}

/* header */
.site-header{position:absolute;left:0;top:0;width:1020px;height:71px;background:var(--white);z-index:3}
.brand{position:absolute;left:137px;top:14px;font-family:"Oswald",sans-serif;font-weight:400;font-size:21px;line-height:22px;color:#111;text-transform:uppercase;letter-spacing:.5px}
.main-nav{position:absolute;left:391px;top:28px;display:flex;gap:28px;font-size:9.5px;font-weight:500;color:#555}
.main-nav .active{color:var(--blue)}
.call-btn{position:absolute;left:742px;top:17px;width:140px;height:35px;border-radius:18px;background:linear-gradient(90deg,var(--blue-deep),var(--blue-light));color:#fff;font-family:"Oswald",sans-serif;font-size:15px;display:flex;align-items:center;justify-content:center;gap:6px}

/* hero */
.hero{position:absolute;left:0;top:71px;width:1020px;height:360px}
.hero-title{position:absolute;left:0;top:160px;width:1020px;text-align:center;font-family:"Oswald",sans-serif;font-weight:400;font-size:52px;color:var(--ink)}

/* form */
.intro{position:absolute;left:0;top:469px;width:1020px;text-align:center;font-size:9px;line-height:16.5px;color:var(--text)}
.field{position:absolute;border:1px solid var(--line);background:#fff;font-size:9.5px;color:#666;padding:0 9px;display:flex;align-items:center}
.field.msg{align-items:flex-start;padding-top:11px}
.label{position:absolute;left:309px;top:608px;font-size:9.5px;color:#333}
.radio{position:absolute;top:628px;font-size:9.5px;color:#555;display:flex;align-items:center;gap:8px}
.radio i{width:10px;height:10px;border:1px solid #e2e2e2;border-radius:50%;display:block}
.submit{position:absolute;left:405px;top:744px;width:210px;height:38px;border-radius:19px;background:linear-gradient(90deg,var(--blue-deep),var(--blue-light));color:#fff;font-family:"Oswald",sans-serif;font-size:17px;display:flex;align-items:center;justify-content:center}

/* contact items */
.ci-icon{position:absolute;width:51px;height:51px;border-radius:50%;background:linear-gradient(135deg,var(--blue-deep),var(--blue-light));display:flex;align-items:center;justify-content:center}
.ci-label{position:absolute;font-size:9.5px;color:#444}
.ci-value{position:absolute;font-family:"Oswald",sans-serif;font-size:15px;color:#111}

/* footer */
.footer-wave{position:absolute;left:0;top:935px;width:1020px;height:265px}
.footer-brand{position:absolute;left:137px;top:1084px;font-family:"Oswald",sans-serif;font-weight:400;font-size:21px;line-height:22px;color:#fff;text-transform:uppercase;letter-spacing:.5px}
.copy{position:absolute;left:138px;top:1146px;width:160px;font-size:9px;line-height:14px;color:var(--muted)}
.copy b{font-weight:400;color:#fff}
.foot-links{position:absolute;left:332px;top:1076px;list-style:none;font-size:9px;color:var(--muted);line-height:22.4px}
.foot-links .active{color:var(--blue)}
.foot-phone{position:absolute;left:546px;top:1064px;font-family:"Oswald",sans-serif;font-size:17px;color:#fff}
.foot-mail{position:absolute;left:541px;top:1106px;font-size:9px;color:var(--muted)}
.social{position:absolute;top:1079px;width:29px;height:29px;border-radius:50%;background:#fff}
.social.first{background:var(--blue)}
</style>
</head>
<body>

<header class="site-header">
  <div class="brand">Tidewell<br>Homecare</div>
  <nav class="main-nav">
    <span>HOME</span><span>SERVICE</span><span>PRICING</span><span>ABOUT US</span><span class="active">CONTACT US</span>
  </nav>
  <div class="call-btn">
    <svg width="12" height="12" viewBox="0 0 24 24"><path fill="#fff" d="M6.6 10.8a15.1 15.1 0 0 0 6.6 6.6l2.2-2.2c.3-.3.7-.4 1-.2 1.1.4 2.3.6 3.6.6.6 0 1 .4 1 1V20c0 .6-.4 1-1 1A17 17 0 0 1 3 4c0-.6.4-1 1-1h3.5c.6 0 1 .4 1 1 0 1.3.2 2.5.6 3.6.1.3 0 .7-.2 1z"/></svg>
    555 014 2290
  </div>
</header>

<svg class="hero" viewBox="0 0 1020 360" role="img" aria-label="Photo of hands typing on a laptop keyboard">
  <defs>
    <linearGradient id="heroFill" x1="0" y1="0" x2="1" y2="1">
      <stop offset="0" stop-color="#eef1f3"/>
      <stop offset=".5" stop-color="#d9dfe3"/>
      <stop offset="1" stop-color="#f1ece8"/>
    </linearGradient>
    <linearGradient id="waveBlue" x1="0" y1="0" x2="1" y2="0">
      <stop offset="0" stop-color="#0680c6"/>
      <stop offset="1" stop-color="#08aef5"/>
    </linearGradient>
  </defs>
  <rect width="1020" height="360" fill="url(#heroFill)"/>
  <path d="M0,280 C170,372 400,366 560,310 C700,262 820,200 940,218 C980,226 1005,248 1020,262 L1020,360 L0,360Z" fill="url(#waveBlue)"/>
  <path d="M0,290 C170,374 400,360 560,320 C700,280 820,222 930,238 C975,245 1005,272 1020,292 L1020,360 L0,360Z" fill="#fff"/>
</svg>
<h1 class="hero-title">Contact Us</h1>

<p class="intro">Lorem Ipsum is simply dummy text of the printing and typesetting industry.<br>Lorem Ipsum has been the industry.</p>

<div class="field" style="left:300px;top:520px;width:204px;height:32px">Enter Name</div>
<div class="field" style="left:516px;top:520px;width:205px;height:32px">Enter Contact No.</div>
<div class="field" style="left:300px;top:564px;width:421px;height:32px">Enter Email</div>
<div class="label">Services Type</div>
<div class="radio" style="left:300px"><i></i>Residential Cleaning</div>
<div class="radio" style="left:427px"><i></i>Commercial Cleaning</div>
<div class="field msg" style="left:300px;top:655px;width:421px;height:76px">Enter Message</div>
<div class="submit">REQUEST MY FREE ESTIMATE</div>

<div class="ci-icon" style="left:281px;top:827px">
  <svg width="20" height="20" viewBox="0 0 24 24"><path fill="#fff" d="M6.6 10.8a15.1 15.1 0 0 0 6.6 6.6l2.2-2.2c.3-.3.7-.4 1-.2 1.1.4 2.3.6 3.6.6.6 0 1 .4 1 1V20c0 .6-.4 1-1 1A17 17 0 0 1 3 4c0-.6.4-1 1-1h3.5c.6 0 1 .4 1 1 0 1.3.2 2.5.6 3.6.1.3 0 .7-.2 1z"/></svg>
</div>
<div class="ci-label" style="left:340px;top:834px">Call Us on</div>
<div class="ci-value" style="left:340px;top:850px">555 014 2290</div>

<div class="ci-icon" style="left:530px;top:827px">
  <svg width="20" height="16" viewBox="0 0 20 16"><rect x="0" y="1" width="20" height="14" rx="2" fill="#fff"/><path d="M1 2 L10 9 L19 2" fill="none" stroke="#0a9ae6" stroke-width="1.6"/></svg>
</div>
<div class="ci-label" style="left:588px;top:834px">Email Us on</div>
<div class="ci-value" style="left:588px;top:850px">info@tidewellhomecare.example</div>

<svg class="footer-wave" viewBox="0 0 1020 265" aria-hidden="true">
  <path d="M0,34 C120,100 250,110 360,96 C500,78 640,10 780,3 C900,-3 980,30 1020,64 L1020,265 L0,265Z" fill="#2a2a2a"/>
</svg>

<div class="footer-brand">Tidewell<br>Homecare</div>
<p class="copy">© <b>Tidewell Homecare</b> - 2020. All Right Reserved.</p>
<ul class="foot-links">
  <li class="active">Home</li><li>Service Offered</li><li>About Us</li><li>Contact Us</li>
</ul>
<svg class="abs" style="left:524px;top:1081px" width="16" height="16" viewBox="0 0 24 24"><path fill="#fff" d="M6.6 10.8a15.1 15.1 0 0 0 6.6 6.6l2.2-2.2c.3-.3.7-.4 1-.2 1.1.4 2.3.6 3.6.6.6 0 1 .4 1 1V20c0 .6-.4 1-1 1A17 17 0 0 1 3 4c0-.6.4-1 1-1h3.5c.6 0 1 .4 1 1 0 1.3.2 2.5.6 3.6.1.3 0 .7-.2 1z"/></svg>
<div class="foot-phone">555 014 2290</div>
<svg class="abs" style="left:524px;top:1116px" width="12" height="10" viewBox="0 0 12 10"><rect x=".5" y=".5" width="11" height="9" rx="1" fill="none" stroke="#8a8a8a"/><path d="M1 1 L6 5.5 L11 1" fill="none" stroke="#8a8a8a"/></svg>
<div class="foot-mail">info@tidewellhomecare.example</div>

<span class="social first" style="left:740px" aria-label="Social link"></span>
<span class="social" style="left:778px" aria-label="Social link"></span>
<span class="social" style="left:816px" aria-label="Social link"></span>
<span class="social" style="left:854px" aria-label="Social link"></span>

</body>
</html>
```